Brightfen Business Card Redesign & Logo Update

We need to update our business cards to something more modern and fresh. Brightfen can provide the current color schemes and old design examples, but welcome creativity in helping us with this redesign. PLEASE NOTE that we no longer utilize the "tree" and/or "leaf" imagery in our branding. If able would apprecaite an update on the quality of our "words only" logo in Ai. / PNG formats too.

Target Market(s)

Investors, landowners, corporate partners, contractors

Industry/Entity Type

Environmental Restoration & Conservation

Contact Information for Business Card

Logo, persons name, title, mailing address, phone and email, website url

Font styles to use
Other font styles liked:
• Merriweather

Requirements
Nice to have
• Logo, persons name, title, mailing address, phone and email, website url, but open to ideams
Should not have
• No all back backgrounds

```html
<!DOCTYPE html>
<html lang="en">
<head>
<meta charset="utf-8">
<title>Brightfen Business Card</title>
<link rel="stylesheet" href="https://fonts.googleapis.com/css2?family=Oswald:wght@300;400;600&display=swap">
<style>
  :root {
    --backdrop: #2d2d2d;
    --card-top: #1c2a22;
    --card-bottom: #0f1813;
    --orange: #ee7a00;
    --green: #1a8a40;
    --rule: #127a35;
    --white: #ffffff;
    --card-w: 560px;
    --card-h: 320px;
  }
  * { box-sizing: border-box; margin: 0; padding: 0; }
  html, body {
    width: 1200px;
    height: 1015px;
    overflow: hidden;
    background: var(--backdrop);
    font-family: "Oswald", sans-serif;
  }
  .sheet {
    width: 1200px;
    height: 1015px;
    display: flex;
    flex-direction: column;
    align-items: center;
    justify-content: center;
    gap: 60px;
  }
  .card {
    position: relative;
    width: var(--card-w);
    height: var(--card-h);
    background: linear-gradient(160deg, var(--card-top), var(--card-bottom));
    box-shadow: 0 10px 24px rgba(0,0,0,0.45);
    overflow: hidden;
  }
  .card__stripe {
    position: absolute;
    left: 0; right: 0; bottom: 0;
    height: 10px;
  }
  .card__stripe--green { background: var(--rule); }
  .card__stripe--orange { background: var(--orange); }

  .wordmark {
    position: absolute;
    display: flex;
    align-items: center;
    gap: 12px;
  }
  .wordmark__square {
    width: 18px;
    height: 18px;
    background: var(--green);
    flex: none;
  }
  .wordmark__name {
    color: var(--orange);
    font-weight: 600;
    line-height: 1;
  }

  /* Front */
  .card--front .wordmark {
    top: 50%; left: 50%;
    transform: translate(-50%, -60%);
  }
  .card--front .wordmark__name { font-size: 56px; }

  /* Back */
  .card--back .wordmark {
    right: 36px;
    top: 66px;
  }
  .card--back .wordmark__name { font-size: 40px; }
  .card--back .wordmark__square { width: 14px; height: 14px; }

  .contact {
    position: absolute;
    left: 34px;
    top: 52px;
    width: 250px;
    color: var(--white);
  }
  .contact__name {
    font-size: 32px;
    font-weight: 600;
    text-transform: uppercase;
    line-height: 1;
    color: var(--orange);
  }
  .contact__name-last { color: var(--green); }
  .contact__title {
    font-size: 15px;
    font-weight: 300;
    text-transform: uppercase;
    letter-spacing: 0.5px;
    margin-top: 4px;
  }
  .contact__rule {
    width: 110px;
    height: 1px;
    background: var(--rule);
    margin: 14px 0 14px 16px;
  }
  .contact__list { list-style: none; padding-left: 22px; }
  .contact__item {
    display: flex;
    align-items: center;
    gap: 10px;
    font-size: 17px;
    font-weight: 300;
    line-height: 1.35;
  }
  .contact__icon { width: 15px; height: 15px; flex: none; }
  .contact__address {
    padding-left: 40px;
    font-size: 17px;
    font-weight: 300;
    line-height: 1.25;
  }
  .contact__rule--lower { margin-left: 34px; }
</style>
</head>
<body>
<main class="sheet">
  <section class="card card--front" aria-label="Business card front">
    <div class="wordmark">
      <span class="wordmark__square"></span>
      <span class="wordmark__name">Brightfen</span>
    </div>
    <div class="card__stripe card__stripe--green"></div>
  </section>

  <section class="card card--back" aria-label="Business card back">
    <div class="contact">
      <h1 class="contact__name">Daniel <span class="contact__name-last">Marsh</span></h1>
      <p class="contact__title">Managing Director</p>
      <div class="contact__rule"></div>
      <ul class="contact__list">
        <li class="contact__item">
          <svg class="contact__icon" viewBox="0 0 24 24" aria-hidden="true"><path fill="#ee7a00" d="M6.6 10.8a15 15 0 0 0 6.6 6.6l2.2-2.2a1 1 0 0 1 1-.25 11.4 11.4 0 0 0 3.6.57 1 1 0 0 1 1 1V20a1 1 0 0 1-1 1A17 17 0 0 1 3 4a1 1 0 0 1 1-1h3.5a1 1 0 0 1 1 1c0 1.25.2 2.45.57 3.57a1 1 0 0 1-.25 1z"/></svg>
          031-482 907 215
        </li>
        <li class="contact__item">
          <svg class="contact__icon" viewBox="0 0 24 24" aria-hidden="true"><path fill="#ee7a00" d="M2 5h20v14H2z"/><path fill="none" stroke="#142019" stroke-width="1.6" d="M2 5l10 8 10-8"/></svg>
          hello@brightfen.com
        </li>
        <li class="contact__item">
          <svg class="contact__icon" viewBox="0 0 24 24" aria-hidden="true"><g fill="none" stroke="#ee7a00" stroke-width="2"><circle cx="12" cy="12" r="10"/><ellipse cx="12" cy="12" rx="4.5" ry="10"/><path d="M2 12h20M4 7h16M4 17h16"/></g></svg>
          www.brightfen.com
        </li>
      </ul>
      <div class="contact__rule contact__rule--lower"></div>
      <p class="contact__address">118, Alder Creek Road<br>30217, Northvale</p>
    </div>
    <div class="wordmark">
      <span class="wordmark__square"></span>
      <span class="wordmark__name">Brightfen</span>
    </div>
    <div class="card__stripe card__stripe--orange"></div>
  </section>
</main>
</body>
</html>
```